Business Card Design for a Software Startup

We'd like to have a business card design. We already have a logo. Basically what we need is a clean design with name, address, cellphone and phone numbers, e-mail and web site address (front) and a space on the back with our logo with the company name on the right side and some texts on the bottom.
We are a development and consulting company in Brazil with highly qualified team of professionals in Java, iOS and Android development and consulting.

Target Market(s)

CIO, IT managers of mid to big size companies

Industry/Entity Type

Business

```html
<!DOCTYPE html>
<html lang="en">
<head>
<meta charset="UTF-8">
<title>Veldar Business Card</title>
<link href="https://fonts.googleapis.com/css2?family=Open+Sans:wght@400;600;700&display=swap" rel="stylesheet">
<style>
  :root {
    --page-bg: #e8eaee;
    --card-white: #ffffff;
    --brand-navy: #123a6e;
    --brand-deep: #1d2f6b;
    --brand-sky: #0aa3e3;
    --brand-mid: #1f6fb8;
    --ink: #333a44;
    --on-blue: #ffffff;
  }
  * { margin: 0; padding: 0; box-sizing: border-box; }
  html, body {
    width: 1200px;
    height: 720px;
    overflow: hidden;
  }
  body {
    background: var(--page-bg);
    font-family: "Open Sans", Arial, sans-serif;
    position: relative;
  }
  .card {
    position: absolute;
    top: 200px;
    width: 560px;
    height: 320px;
    overflow: hidden;
    box-shadow: 0 6px 18px rgba(20, 30, 60, 0.18);
  }
  .card--front { left: 27px; background: var(--card-white); }
  .card--back { left: 613px; }
  .card-art {
    position: absolute;
    inset: 0;
    width: 100%;
    height: 100%;
  }

  /* Front */
  .holder {
    position: absolute;
    top: 28px;
    right: 170px;
    text-align: right;
    color: var(--brand-navy);
  }
  .holder-name {
    font-weight: 700;
    font-size: 21px;
    line-height: 1.1;
  }
  .holder-title {
    font-size: 12px;
    color: var(--ink);
  }
  .brand {
    position: absolute;
    left: 44px;
    top: 128px;
    display: flex;
    align-items: center;
    gap: 12px;
  }
  .brand-square {
    width: 42px;
    height: 42px;
    background: var(--brand-mid);
  }
  .brand-name {
    font-weight: 700;
    font-size: 38px;
    letter-spacing: 1px;
    color: var(--brand-navy);
  }
  .address {
    position: absolute;
    left: 62px;
    top: 222px;
    font-size: 13px;
    font-style: normal;
    line-height: 1.5;
    color: var(--ink);
  }
  .contact {
    position: absolute;
    right: 24px;
    top: 130px;
    list-style: none;
    color: var(--on-blue);
    font-size: 12px;
    line-height: 1.6;
    text-align: right;
  }
  .contact li {
    display: flex;
    justify-content: flex-end;
    align-items: center;
    gap: 6px;
  }
  .contact svg { width: 11px; height: 11px; flex: none; }

  /* Back */
  .back-brand {
    position: absolute;
    left: 0;
    right: 0;
    top: 112px;
    display: flex;
    justify-content: center;
    align-items: center;
    gap: 16px;
  }
  .back-brand-square {
    width: 58px;
    height: 58px;
    background: var(--on-blue);
    border-radius: 8px;
  }
  .back-brand-name {
    font-weight: 700;
    font-size: 52px;
    letter-spacing: 2px;
    color: var(--on-blue);
  }
  .back-web {
    position: absolute;
    right: 70px;
    bottom: 34px;
    color: var(--on-blue);
    font-size: 15px;
    letter-spacing: 4px;
  }
</style>
</head>
<body>

  <section class="card card--front" aria-label="Business card front">
    <svg class="card-art" viewBox="0 0 560 320" preserveAspectRatio="none" aria-hidden="true">
      <defs>
        <linearGradient id="frontBlue" x1="0" y1="1" x2="1" y2="0">
          <stop offset="0" stop-color="#0aa3e3"/>
          <stop offset="0.55" stop-color="#1f5fae"/>
          <stop offset="1" stop-color="#243775"/>
        </linearGradient>
      </defs>
      <path d="M400 0 L560 0 L560 320 L200 320 C360 260 430 110 400 0 Z" fill="#123a6e"/>
      <path d="M425 0 L560 0 L560 320 L225 320 C385 260 455 110 425 0 Z" fill="url(#frontBlue)"/>
    </svg>

    <div class="holder">
      <p class="holder-name">Your Name</p>
      <p class="holder-title">Title</p>
    </div>

    <div class="brand">
      <span class="brand-square"></span>
      <span class="brand-name">VELDAR</span>
    </div>

    <address class="address">
      Door No. Street Name<br>
      City Name, State, Zip Code
    </address>

    <ul class="contact">
      <li>
        <svg viewBox="0 0 12 12"><circle cx="6" cy="6" r="5.3" fill="none" stroke="#fff" stroke-width="1.2"/><path d="M4 3.5 L5 3.5 L5.5 5 L4.8 5.6 Q5.6 7 6.6 7.4 L7.2 6.7 L8.6 7.2 L8.6 8.2 Q5 8.6 3.6 4.2 Z" fill="#fff"/></svg>
        555-010-2468
      </li>
      <li>
        <svg viewBox="0 0 12 12"><rect x="3.5" y="1" width="5" height="10" rx="1" fill="none" stroke="#fff" stroke-width="1.2"/><rect x="4.6" y="2.5" width="2.8" height="4.5" fill="#fff"/></svg>
        555-013-9753
      </li>
      <li>
        <svg viewBox="0 0 12 12"><rect x="1" y="2.5" width="10" height="7" fill="#fff"/><path d="M1 2.5 L6 6.5 L11 2.5" fill="none" stroke="#1f5fae" stroke-width="1"/></svg>
        yourname@veldar.com
      </li>
      <li>
        <svg viewBox="0 0 12 12"><circle cx="6" cy="6" r="5" fill="none" stroke="#fff" stroke-width="1.2"/><ellipse cx="6" cy="6" rx="2" ry="5" fill="none" stroke="#fff" stroke-width="1"/><path d="M1 6 H11" stroke="#fff" stroke-width="1"/></svg>
        www.veldar.com
      </li>
    </ul>
  </section>

  <section class="card card--back" aria-label="Business card back">
    <svg class="card-art" viewBox="0 0 560 320" preserveAspectRatio="none" aria-hidden="true">
      <defs>
        <linearGradient id="backBlue" x1="0" y1="1" x2="1" y2="0">
          <stop offset="0" stop-color="#0aa8e8"/>
          <stop offset="0.5" stop-color="#1d6cb8"/>
          <stop offset="1" stop-color="#2b3471"/>
        </linearGradient>
      </defs>
      <rect width="560" height="320" fill="url(#backBlue)"/>
    </svg>

    <div class="back-brand">
      <span class="back-brand-square"></span>
      <span class="back-brand-name">VELDAR</span>
    </div>

    <p class="back-web">www.veldar.com</p>
  </section>

</body>
</html>
```